wealth management firm, professional group, new model

we have a logo that works but we need a card, white background using our colors...clean look

our tag line if can be used in

The Bridge From Client to Owner

```html
<!DOCTYPE html>
<html lang="en">
<head>
<meta charset="UTF-8">
<title>Arcova Wealth Partners – Business Card</title>
<link href="https://fonts.googleapis.com/css2?family=Lexend:wght@300;400&family=Montserrat:wght@400&display=swap" rel="stylesheet">
<style>
  :root {
    --navy: #142a4c;
    --paper: #ffffff;
    --paper-shade: #ececed;
    --step-grey: #c3c5c9;
    --ink: #2e3440;
    --backdrop: #e9e6e1;
  }
  * { margin: 0; padding: 0; box-sizing: border-box; }
  html, body {
    width: 1200px; height: 900px; overflow: hidden;
    background: var(--backdrop);
    font-family: "Lexend", sans-serif;
  }
  .sheet {
    width: 1200px; height: 900px;
    display: flex; flex-direction: column; align-items: center; justify-content: center;
    gap: 48px;
  }
  .card {
    position: relative;
    width: 640px; height: 366px;
    overflow: hidden;
    box-shadow: 0 6px 18px rgba(0,0,0,0.18);
  }
  .card--front {
    background: var(--navy);
    display: flex; align-items: center; justify-content: center;
  }
  .card--back {
    background: linear-gradient(115deg, var(--paper-shade) 0%, var(--paper) 70%);
  }
  .brand {
    display: flex; align-items: center; gap: 12px;
    font-family: "Montserrat", sans-serif;
    font-weight: 400;
    letter-spacing: 0.12em;
    text-transform: uppercase;
  }
  .brand__dot {
    width: 12px; height: 12px; border-radius: 50%;
  }
  .card--front .brand { color: var(--paper); font-size: 22px; }
  .card--front .brand__dot { background: var(--paper); }
  .card--back .brand {
    position: absolute; top: 74px; right: 40px;
    color: var(--navy); font-size: 17px;
  }
  .card--back .brand__dot { background: var(--navy); }
  .card__band { position: absolute; inset: 0; }
  .holder {
    position: absolute; left: 36px; top: 42px;
    color: var(--paper);
  }
  .holder__name { font-size: 17px; font-weight: 400; text-transform: uppercase; }
  .holder__role { font-size: 14px; font-weight: 300; margin-top: 2px; }
  .address {
    position: absolute; right: 40px; top: 196px;
    text-align: right; color: var(--ink);
    font-size: 14px; font-weight: 300; line-height: 1.45;
  }
  .contacts {
    position: absolute; left: 48px; bottom: 38px;
    list-style: none; color: var(--ink);
    font-size: 14px; font-weight: 300;
  }
  .contacts__item { display: flex; align-items: center; gap: 10px; line-height: 1.75; }
  .contacts__icon { width: 15px; height: 15px; flex: none; }
</style>
</head>
<body>
<main class="sheet">

  <section class="card card--front" aria-label="Card front">
    <div class="brand"><span class="brand__dot"></span>Arcova Wealth Partners</div>
  </section>

  <section class="card card--back" aria-label="Card back">
    <svg class="card__band" viewBox="0 0 640 366" aria-hidden="true">
      <polygon points="0,0 640,0 640,38 306,38 292,112 0,112" fill="var(--step-grey)"/>
      <polygon points="0,0 640,0 640,26 290,26 276,100 0,100" fill="var(--navy)"/>
    </svg>

    <div class="holder">
      <div class="holder__name">Daniel Hart</div>
      <div class="holder__role">Director</div>
    </div>

    <div class="brand"><span class="brand__dot"></span>Arcova Wealth Partners</div>

    <address class="address" style="font-style:normal">
      00 dummy city<br>dummy place 0000
    </address>

    <ul class="contacts">
      <li class="contacts__item">
        <svg class="contacts__icon" viewBox="0 0 24 24" aria-hidden="true"><path fill="var(--navy)" d="M6.6 10.8a15 15 0 0 0 6.6 6.6l2.2-2.2c.3-.3.7-.4 1-.2 1.1.4 2.3.6 3.6.6.6 0 1 .4 1 1V20c0 .6-.4 1-1 1A17 17 0 0 1 3 4c0-.6.4-1 1-1h3.5c.6 0 1 .4 1 1 0 1.3.2 2.5.6 3.6.1.3 0 .7-.2 1z"/></svg>
        410-555-0182
      </li>
      <li class="contacts__item">
        <svg class="contacts__icon" viewBox="0 0 24 24" aria-hidden="true"><rect x="2" y="5" width="20" height="14" fill="var(--navy)"/><polyline points="2,5 12,13 22,5" fill="none" stroke="var(--paper)" stroke-width="1.6"/></svg>
        hello@arcovawealth.com
      </li>
      <li class="contacts__item">
        <svg class="contacts__icon" viewBox="0 0 24 24" aria-hidden="true"><g fill="none" stroke="var(--navy)" stroke-width="1.6"><circle cx="12" cy="12" r="9"/><ellipse cx="12" cy="12" rx="4" ry="9"/><line x1="3" y1="12" x2="21" y2="12"/></g></svg>
        www.arcovawealth.com
      </li>
    </ul>
  </section>

</main>
</body>
</html>
```